Business Card Design for Occupational Medicine Start Up Company

We need to design a professional business card. We are a healthcare company providing occupational medicine services to blue collar industries. We are professional, efficient and high quality service providers.

Target Market(s)

Blue Collar Industry: Shipbuilding, Ports, Trucking Companies; The Executives and Safety Officers for these companies

Industry/Entity Type

Healthcare

Contact Information for Business Card

Logo, Name, Title, Email, Phone

Other font styles liked:
• Please match our Brand Guide

Requirements
Must have
• Our Company Colors and Logo

```html
<!DOCTYPE html>
<html lang="en">
<head>
<meta charset="utf-8">
<title>Shiftwell Clinics – Business Card</title>
<link rel="stylesheet" href="https://fonts.googleapis.com/css2?family=Montserrat:wght@400;500;700&display=swap">
<style>
  :root {
    --backdrop: #262626;
    --paper: #f7f7f5;
    --navy: #2e2f7f;
    --navy-soft: #3a3c92;
    --sky: #2fa3dc;
    --amber: #eca93a;
  }
  * { margin: 0; padding: 0; box-sizing: border-box; }
  html, body { width: 1200px; height: 1200px; overflow: hidden; }
  body {
    background: var(--backdrop);
    font-family: "Montserrat", Arial, sans-serif;
    position: relative;
  }
  .card {
    position: absolute;
    left: 303px;
    width: 594px;
    height: 348px;
    background: var(--paper);
    border-radius: 24px;
    overflow: hidden;
  }
  .card--front { top: 190px; }
  .card--back { top: 650px; }

  .brand { position: absolute; display: flex; flex-direction: column; align-items: center; }
  .brand__dot { border-radius: 50%; background: var(--sky); }
  .brand__name {
    color: var(--navy);
    font-weight: 700;
    letter-spacing: 0.5px;
    text-transform: uppercase;
    white-space: nowrap;
  }
  .card--front .brand { left: 0; right: 0; top: 78px; }
  .card--front .brand__dot { width: 70px; height: 70px; margin-bottom: 26px; }
  .card--front .brand__name { font-size: 32px; }
  .front__url {
    position: absolute; left: 0; right: 0; top: 302px;
    text-align: center; font-size: 15px; color: var(--navy); letter-spacing: 1px;
  }

  .card--back .brand { left: 40px; width: 260px; top: 48px; }
  .card--back .brand__dot { width: 86px; height: 86px; margin-bottom: 40px; }
  .card--back .brand__name { font-size: 23px; }

  .band {
    position: absolute; left: 0; right: 0; bottom: 0; height: 112px;
    background: linear-gradient(90deg, var(--navy-soft) 0%, var(--navy) 100%);
  }

  .person { position: absolute; right: 30px; top: 42px; text-align: right; color: var(--navy); }
  .person__name { font-size: 24px; font-weight: 500; color: var(--sky); letter-spacing: 0.5px; }
  .person__title { font-size: 15px; margin-top: 1px; }
  .person__address { font-size: 15px; line-height: 21px; margin-top: 20px; }

  .contact {
    position: absolute; right: 30px; top: 256px;
    list-style: none; color: #fff; font-size: 15px; line-height: 21px;
  }
  .contact li { display: flex; justify-content: flex-end; align-items: center; gap: 12px; }
  .contact svg { width: 14px; height: 14px; flex: none; }
</style>
</head>
<body>

<section class="card card--front">
  <div class="brand">
    <span class="brand__dot"></span>
    <span class="brand__name">Shiftwell Clinics</span>
  </div>
  <p class="front__url">www.shiftwellclinics.com</p>
</section>

<section class="card card--back">
  <div class="band" role="img" aria-label="Decorative brand-colour band along the bottom of the card"></div>

  <div class="brand">
    <span class="brand__dot"></span>
    <span class="brand__name">Shiftwell Clinics</span>
  </div>

  <div class="person">
    <h1 class="person__name">DANA REYES</h1>
    <p class="person__title">Senior Doctor</p>
    <p class="person__address">48 Harbor Lane, Suite 210<br>Portside, State 54321</p>
  </div>

  <ul class="contact">
    <li>555-014-2290
      <svg viewBox="0 0 14 14"><path d="M2,5 C2,2 12,2 12,5 L10,6 L9,4.5 L5,4.5 L4,6 Z M3,7 L11,7 L12,12 L2,12 Z" fill="var(--sky)"/></svg>
    </li>
    <li>www.shiftwell.com
      <svg viewBox="0 0 14 14"><rect x="1" y="3" width="12" height="8" fill="#fff"/><path d="M1,3 L7,8 L13,3" fill="none" stroke="var(--navy)" stroke-width="1.2"/></svg>
    </li>
    <li>dana@shiftwell.com
      <svg viewBox="0 0 14 14"><circle cx="7" cy="7" r="6" fill="var(--amber)"/><path d="M1,7 H13 M7,1 V13 M7,1 C3,4 3,10 7,13 M7,1 C11,4 11,10 7,13" fill="none" stroke="var(--navy)" stroke-width="0.8"/></svg>
    </li>
  </ul>
</section>

</body>
</html>
```